Organization and people consulting firm needs a website design

I need a website that promotes and explains the consulting service we will provide. The organization is called Bluefinch Advisory Partners. Our services include organization design, employee experience, change management, and executive coaching. I would like to see a simple clean and professional design, that reflects a modern and forward looking professional services company

Target Market(s)

Mid market and large companies

Industry/Entity Type

Management Consulting

Coding

Coded - Design and coding required

Number of Pages Required

5+ page

Font styles to use
Sans Serif

Colors

Designer to choose colors to be used in the design.

Requirements
Must have
• The following pages: Home, The Way We Work, What We Do, Our Founder, Insights, Contact.
• Search button.
• Hyper links (will be provided with main body text)
• Scrolling website with summaries at top level and links to more detail at lower level (like this website: veltracore.com)
• Company logo (uploaded)
• I have text for each of the pages that I can upload once the basic design is done
Should not have
• No clutter, keep the design clean

```html
<!DOCTYPE html>
<html lang="en">
<head>
<meta charset="utf-8">
<title>Bluefinch Advisory Partners</title>
<link href="https://fonts.googleapis.com/css2?family=Lato:wght@300;400;700&display=swap" rel="stylesheet">
<style>
:root{
  --red:#e31e3a;
  --red-soft:#f6d3d8;
  --ink:#333;
  --muted:#777;
  --bg:#fafafa;
  --grey:#efefef;
  --white:#fff;
}
*{box-sizing:border-box;margin:0;padding:0}
html,body{width:1200px;height:3947px;overflow:hidden}
body{font-family:'Lato',sans-serif;color:var(--ink);background:var(--bg);position:relative}
.site-header{height:95px;background:var(--white);position:relative}
.brand{position:absolute;left:105px;top:30px;display:flex;align-items:center;gap:10px;color:var(--red);font-size:26px;font-weight:700}
.brand-dot{width:22px;height:22px;border-radius:50%;background:var(--red)}
.main-nav{position:absolute;top:40px;left:0;width:100%;font-size:14px}
.main-nav a{position:absolute;color:var(--ink);text-decoration:none}
.main-nav a.active{color:var(--red)}
.search{position:absolute;left:1088px;top:40px}
.hero{height:578px;position:relative;background:linear-gradient(120deg,#d94a5b,#e4707c 50%,#c93c4f);text-align:center;color:var(--white)}
.hero h1{position:absolute;top:160px;width:100%;font-weight:300;font-size:62px;letter-spacing:2px}
.hero p{position:absolute;top:238px;width:100%;font-weight:300;font-size:22px;letter-spacing:5px}
.hero-arrow{position:absolute;top:270px;width:44px;height:44px;border-radius:50%;background:rgba(255,255,255,.25);display:flex;align-items:center;justify-content:center}
.section{position:relative;text-align:center}
.section h2{position:absolute;width:100%;font-weight:300;font-size:54px;color:var(--red)}
.divider{position:absolute;left:588px;width:24px;height:3px;background:var(--red-soft)}
.lead{position:absolute;left:50%;transform:translateX(-50%);width:860px;font-weight:300;font-size:21px;line-height:34px;color:var(--muted)}
.btn{position:absolute;left:518px;width:165px;height:52px;background:var(--red);color:var(--white);font-size:15px;line-height:52px;text-transform:uppercase;text-decoration:none}
.services .service{position:absolute;width:220px;margin-left:-110px;top:249px}
.service .ring{width:110px;height:110px;border-radius:50%;margin:0 auto;background:var(--white);box-shadow:0 0 0 2px #f7e6e9;display:flex;align-items:center;justify-content:center}
.service.active .ring{background:var(--red);box-shadow:none}
.service h3{margin-top:24px;font-weight:400;font-size:20px}
.service.active h3{color:var(--red)}
.service p{margin-top:10px;font-size:12px;line-height:18px;color:var(--muted);padding:0 25px}
.portrait{position:absolute;left:484px;top:326px;width:232px;height:232px;border-radius:50%;background:var(--red-soft);display:flex;align-items:center;justify-content:center}
.portrait div{width:188px;height:188px;border-radius:50%;background:linear-gradient(160deg,#7a6a62,#3a4156)}
.founder-name{position:absolute;width:100%;top:576px;font-size:23px;color:var(--red)}
.founder-role{position:absolute;width:100%;top:612px;font-size:16px;color:var(--muted)}
.contact-line{position:absolute;width:100%;font-size:15px;color:var(--muted)}
.contact-item{position:absolute;top:326px;display:flex;align-items:center;gap:22px;font-size:14px}
.contact-item .dot{width:36px;height:36px;border-radius:50%;background:var(--white);box-shadow:0 1px 4px rgba(0,0,0,.1);display:flex;align-items:center;justify-content:center}
.site-footer{position:absolute;top:3860px;left:0;width:1200px;height:87px;background:var(--red);color:var(--white);font-size:13px}
.site-footer p{position:absolute;top:36px;width:100%;text-align:center}
.site-footer span{position:absolute;right:40px;top:36px}
</style>
</head>
<body>
<header class="site-header">
  <div class="brand"><span class="brand-dot"></span>Bluefinch</div>
  <nav class="main-nav">
    <a class="active" style="left:479px">Home</a>
    <a style="left:556px">The Way We Work</a>
    <a style="left:698px">What We Do</a>
    <a style="left:809px">Our Founder</a>
    <a style="left:921px">Insights</a>
    <a style="left:1006px">Contact</a>
  </nav>
  <svg class="search" width="14" height="14" viewBox="0 0 14 14"><circle cx="6" cy="6" r="4.5" fill="none" stroke="#333" stroke-width="2"/><line x1="9.5" y1="9.5" x2="13" y2="13" stroke="#333" stroke-width="2"/></svg>
</header>

<section class="hero" role="img" aria-label="Photo of a businessman leaning back with hands behind his head, red overlay">
  <h1>Bluefinch Advisory Partners</h1>
  <p>We are organisation &amp; people consulting firm</p>
  <div class="hero-arrow" style="left:22px"><svg width="14" height="14" viewBox="0 0 14 14"><path d="M9 2 4 7l5 5" fill="none" stroke="#fff" stroke-width="2"/></svg></div>
  <div class="hero-arrow" style="right:22px"><svg width="14" height="14" viewBox="0 0 14 14"><path d="M5 2l5 5-5 5" fill="none" stroke="#fff" stroke-width="2"/></svg></div>
</section>

<section class="section" style="height:540px;background:var(--bg)">
  <h2 style="top:82px">The Way We Work</h2>
  <span class="divider" style="top:180px"></span>
  <p class="lead" style="top:218px">Lorem ipsum dolor sit amet, consectetur adipiscing elit, sed do eiusmod tempor incididunt ut labore et dolore magna aliqua. Ut enim ad minim veniam, quis nostrud exercitation ullamco laboris nisi ut aliquip ex ea commodo consequat.</p>
  <a class="btn" style="top:379px">Learn more</a>
</section>

<section class="section services" style="height:595px;background:#f4f4f4">
  <h2 style="top:73px">What We Do</h2>
  <span class="divider" style="top:170px"></span>
  <div class="service" style="left:187px"><div class="ring"><svg width="48" height="40" viewBox="0 0 48 40" fill="none" stroke="#e31e3a" stroke-width="1.5"><circle cx="24" cy="7" r="4"/><circle cx="10" cy="22" r="3.5"/><circle cx="24" cy="22" r="3.5"/><circle cx="38" cy="22" r="3.5"/><path d="M4 38v-5a6 6 0 0 1 12 0v5M18 38v-5a6 6 0 0 1 12 0v5M32 38v-5a6 6 0 0 1 12 0v5M24 11v5M10 16h28"/></svg></div><h3>Organisation design</h3></div>
  <div class="service" style="left:461px"><div class="ring"><svg width="44" height="34" viewBox="0 0 44 34" fill="none" stroke="#e31e3a" stroke-width="1.5"><path d="M2 12l10-6 10 4 10-4 10 6-8 12-10 6-12-10z"/><path d="M14 18l6 5M18 15l6 5"/></svg></div><h3>Employee experience</h3></div>
  <div class="service active" style="left:737px"><div class="ring"><svg width="50" height="44" viewBox="0 0 50 44" fill="none" stroke="#fff" stroke-width="1.5"><circle cx="25" cy="8" r="4"/><circle cx="9" cy="34" r="4"/><circle cx="41" cy="34" r="4"/><path d="M17 14a14 14 0 0 0-8 14M33 14a14 14 0 0 1 8 14M15 40h20"/></svg></div><h3>Change management</h3><p>Sed quia non numquam eius modi tempora incidunt ut labore et dolore magnam aliquam quaerat voluptatem.</p></div>
  <div class="service" style="left:1008px"><div class="ring"><svg width="36" height="40" viewBox="0 0 36 40" fill="none" stroke="#e31e3a" stroke-width="1.5"><circle cx="18" cy="18" r="13"/><path d="M13 33v5h10v-5M18 11v14M13 16l5 5 5-5"/></svg></div><h3>Executive coaching</h3></div>
</section>

<section class="section" style="height:872px;background:var(--bg)">
  <h2 style="top:64px">Our Founder</h2>
  <span class="divider" style="top:160px"></span>
  <p class="lead" style="top:208px;width:840px">At vero eos et accusamus et iusto odio dignissimos ducimus qui blanditiis praesentium voluptatum deleniti atque corrupti quos dolores et quas molestias excepturi sint occaecati cupiditate non provident, similique sunt in culpa qui officia deserunt mollitia animi.</p>
  <div class="portrait"><div role="img" aria-label="Portrait photo of the founder"></div></div>
  <p class="founder-name">Exercitationem Ullam</p>
  <p class="founder-role">Founder</p>
  <a class="btn" style="top:712px">More about me</a>
</section>

<section class="section" style="height:570px;background:var(--grey)">
  <h2 style="top:80px">Our Insights</h2>
  <span class="divider" style="top:176px"></span>
  <p class="lead" style="top:228px;width:880px">But I must explain to you how all this mistaken idea of denouncing pleasure and praising pain was born and I will give you a complete account of the system, and expound the actual teachings of the great explorer of the truth.</p>
  <a class="btn" style="top:398px">Learn more</a>
</section>

<section class="section" style="height:610px;background:var(--bg)">
  <h2 style="top:70px">Contact Us</h2>
  <span class="divider" style="top:168px"></span>
  <p class="contact-line" style="top:212px;letter-spacing:1px">GET IN TOUCH WITH US AND SEE HOW WE CAN HELP</p>
  <p class="contact-line" style="top:253px;color:var(--ink)">Daniel Marsh, 48 Elm Ridge Lane, Westbrook, CT 06498, U.S.A</p>
  <div class="contact-item" style="left:142px"><span class="dot"><svg width="12" height="12" viewBox="0 0 12 12"><path d="M2 1h3l1 3-2 1a7 7 0 0 0 3 3l1-2 3 1v3c-6 0-9-3-9-9z" fill="#e31e3a"/></svg></span>+1-555-014-2290</div>
  <div class="contact-item" style="left:402px"><span class="dot"><svg width="14" height="10" viewBox="0 0 14 10"><rect width="14" height="10" fill="#e31e3a"/><path d="M0 0l7 5 7-5" fill="none" stroke="#fff"/></svg></span>daniel.marsh@bluefinchadvisorypartners.com</div>
  <div class="contact-item" style="left:834px"><span class="dot"><svg width="12" height="12" viewBox="0 0 12 12"><circle cx="6" cy="6" r="6" fill="#e31e3a"/></svg></span>bluefinchadvisorypartners.com</div>
  <a class="btn" style="top:455px">Get in touch</a>
</section>

<footer class="site-footer">
  <p>© 2018 Bluefinch Advisory Partners. All right reserved. Term of Use</p>
  <span>CSR</span>
</footer>
</body>
</html>
```